RevelHubQZ Business Cards

Front
Has logo with a design. Website address (www.revelhubqz-example.net)
Has slogan (discover the nightlife)
Has phone number (5182297734)
Should be bold and stands out.

Back
Has details about what we offer.

Events
Search upcoming events
Submit events
Party Image Gallery
View and download HQ party images
Sign up as a contributing event photographer and get paid!
Tickets
Sell your event tickets online for free!
Direct pay
No ticket fee

Target Market(s)

These cards will be handed out in clubs and events to patrons.

Industry/Entity Type

Business

Contact Information for Business Card

Should match or mirror our website in some sort of way. Visit the website to get ideas.

Requirements
Must have
• Must be designed for a 3x3 inch card.

```html
<!DOCTYPE html>
<html lang="en">
<head>
<meta charset="utf-8">
<title>RevelHubQZ Business Cards</title>
<link href="https://fonts.googleapis.com/css2?family=Mulish:wght@400;700;800&display=swap" rel="stylesheet">
<style>
  :root {
    --page: #e0e0de;
    --card: #fafafa;
    --blue: #00a8e6;
    --pink: #e03c8e;
    --ink: #333333;
    --white: #ffffff;
  }
  * { margin: 0; padding: 0; box-sizing: border-box; }
  html, body { width: 1200px; height: 659px; overflow: hidden; }
  body {
    background: var(--page);
    font-family: "Mulish", "Century Gothic", sans-serif;
    position: relative;
  }
  .card {
    position: absolute;
    top: 142px;
    width: 374px;
    height: 373px;
    background: var(--card);
    overflow: hidden;
  }
  .card--front { left: 201px; }
  .card--back { left: 623px; }

  .card__shapes { position: absolute; inset: 0; }

  .brand {
    position: absolute;
    top: 38px;
    left: 0;
    width: 100%;
    text-align: center;
  }
  .brand__dot {
    display: block;
    width: 46px;
    height: 46px;
    margin: 0 auto 14px;
    border-radius: 50%;
    background: var(--blue);
  }
  .brand__name {
    font-size: 27px;
    font-weight: 700;
    color: var(--blue);
    letter-spacing: -0.5px;
    line-height: 1;
  }
  .brand__tagline {
    margin-top: 5px;
    font-size: 8px;
    letter-spacing: 4px;
    color: var(--ink);
    font-weight: 400;
  }

  .contact {
    position: absolute;
    top: 226px;
    left: 0;
    width: 100%;
    text-align: center;
    color: var(--white);
  }
  .contact__name { font-size: 21px; font-weight: 800; line-height: 1.1; }
  .contact__role { font-size: 12px; margin-top: 2px; }
  .contact__lines { margin-top: 14px; font-size: 14px; line-height: 16.5px; letter-spacing: 0.3px; }

  .strip {
    position: absolute;
    left: 0;
    width: 100%;
  }
  .strip--front {
    bottom: 0;
    height: 15px;
    background: linear-gradient(to bottom, var(--blue), #bfe9f8);
  }
  .strip--back {
    bottom: 0;
    height: 31px;
    background: linear-gradient(to bottom, var(--pink) 0%, var(--pink) 30%, var(--blue) 55%, var(--blue) 100%);
  }

  .offer {
    position: absolute;
    top: 44px;
    left: 0;
    width: 100%;
    text-align: center;
    color: var(--ink);
  }
  .offer__title {
    font-size: 16px;
    font-weight: 800;
    color: var(--pink);
    letter-spacing: 0.5px;
    margin-bottom: 16px;
  }
  .offer__list { list-style: none; font-size: 14.5px; line-height: 21.5px; letter-spacing: 0.2px; }
</style>
</head>
<body>

<section class="card card--front">
  <svg class="card__shapes" viewBox="0 0 374 373" width="374" height="373" aria-hidden="true">
    <path d="M0 216 Q187 174 374 216 V373 H0 Z" fill="var(--blue)"/>
    <path d="M0 211 Q187 169 374 211" fill="none" stroke="var(--pink)" stroke-width="4"/>
  </svg>

  <div class="brand">
    <span class="brand__dot"></span>
    <div class="brand__name">RevelHubQZ</div>
    <div class="brand__tagline">discover the nightlife</div>
  </div>

  <div class="contact">
    <div class="contact__name">Dana Whitfield</div>
    <div class="contact__role">Managing Director</div>
    <div class="contact__lines">
      <div>5182297734</div>
      <div>support@revelhubqz-example.net</div>
      <div>www.revelhubqz-example.net</div>
    </div>
  </div>

  <div class="strip strip--front" role="img" aria-label="Equalizer bar pattern in blue"></div>
</section>

<section class="card card--back">
  <div class="offer">
    <h2 class="offer__title">WE OFFER</h2>
    <ul class="offer__list">
      <li>Events</li>
      <li>Search upcoming events</li>
      <li>Submit events</li>
      <li>Party Image Gallery</li>
      <li>View and download HQ party images</li>
      <li>Sign up as a contributing event</li>
      <li>photographer and get paid!</li>
      <li>Tickets</li>
      <li>Sell your event tickets online for free!</li>
      <li>Direct pay</li>
      <li>No ticket fee</li>
    </ul>
  </div>

  <div class="strip strip--back" role="img" aria-label="Equalizer bar pattern in pink and blue"></div>
</section>

</body>
</html>
```